High-end executive coaching group needs a 2 page digital flyer

We need a 2 page digital flyer for a high end leadership coaching offering for global leaders in healthcare. The flyer will advertise a new service (an elite senior leadership coaching group) for senior leaders in the healthcare industry from around the world.
The flyer should be upmarket, professional and minimalist in style to meet the expectations of my professional market (very senior doctors and executives).
The design should be based on my existing logo and brand, see my landing page: www.marlowadvisory.com
The key elements needed are
1) An editable PDF which we can update as we revise the specific details of the offering. The text and draft design for this is attached.
2) The banner image should be high quality but abstract. It can be based on the landing page of my website (the two ripple effects) but does not need to strictly adhere to this.
3) The logo placement of the Marlow Advisory delta sign should be discreet so that it does not dominate
4) The small logos of our professional accrediting organisations should be discreetly placed at the end and should not dominate. They might work best as mono icons in a footer (e.g. blue on a white background, or white on blue.
5) Please find enclosed a previous flyer as an example of a similar style we have used for more junior professionals. The design worked quite well, although we now need a more upmarket version for our senior executives.

Please note this design specifically needs to use existing branding and images from my website: marlowadvisory.com. We are definitely not looking for stock "leadership team" images for this high-end brochure.

Target Market(s)

Senior global leaders in the healthcare industry

Industry/Entity Type

Leading business schools & Healthcare industry.

Font styles to use
Other font styles liked:
• Operetta (selective use for heading) and Sofia Pro (body text)

Colors
0054AA
0677BA
7BADD7
CADEEF
E8F1F8

Requirements
Must have
• Clean minimalist and high professionally look that directly speaks to the interests and perspectives of senior leader leaders in healthcare. It also needs very clear call to action sections
Nice to have
• Effective presentation of the two bios and photographs. These need to look impressive, but should not dominate.
Should not have
• Loud and bold colours, large use of logos.

```html
<!DOCTYPE html>
<html lang="en">
<head>
<meta charset="utf-8">
<title>Marlow Advisory – Elevate and Ignite Your Leadership</title>
<link href="https://fonts.googleapis.com/css2?family=Poppins:wght@300;400;500;600;700;800&display=swap" rel="stylesheet">
<style>
:root{
  --navy:#283a8f;
  --blue:#3c62c4;
  --sky:#5b8fe0;
  --ink:#151515;
  --grey:#d9d9d9;
  --card:#ececec;
  --paper:#ffffff;
  --backdrop:#efefef;
}
*{margin:0;padding:0;box-sizing:border-box}
html,body{width:783px;height:1200px;overflow:hidden;background:var(--backdrop);font-family:'Poppins',sans-serif;color:var(--ink)}
.sheet{position:absolute;left:171px;width:440px;height:568px;box-shadow:0 2px 8px rgba(0,0,0,.15);overflow:hidden}
.sheet--front{top:24px}
.sheet--back{top:608px}
.page{position:absolute;left:0;top:0;width:653px;height:843px;transform:scale(.6738);transform-origin:0 0;background:var(--paper);overflow:hidden}
.abs{position:absolute}

/* front */
.brand{left:36px;top:44px;font-size:27px;font-weight:400;color:var(--blue);line-height:1}
.headline{left:31px;top:112px;line-height:1}
.headline .l1{font-size:36px;font-weight:800;letter-spacing:.5px}
.headline .l1 span{font-weight:400}
.headline .l2{font-size:36px;font-weight:300}
.headline .l3{font-size:47px;font-weight:800;color:var(--blue)}
.band{left:0;top:242px;width:653px;height:108px;background:var(--navy)}
.band p{position:absolute;left:33px;width:270px;color:#fff;font-size:12.5px;line-height:1.2}
.art{left:0;top:0;width:653px;height:360px}
.panel{left:346px;top:330px;width:278px;height:306px;background:var(--grey);border-radius:0 0 10px 10px}
.intro{left:33px;top:372px;width:280px}
.kicker{font-size:14px;font-weight:700;color:var(--blue);line-height:1.2}
.kicker b{color:var(--ink);display:block;font-weight:700}
.intro p{font-size:9px;line-height:1.25;margin-top:8px}
.intro p.just{text-align:justify;margin-top:14px}
.quote{left:33px;top:518px;width:281px;height:123px;background:var(--blue);border-radius:6px;color:#fff;font-size:9.5px;line-height:1.2;padding:40px 16px 0}
.quote .mark{position:absolute;left:14px;top:-18px;font-size:46px;font-weight:700;color:#fff;-webkit-text-stroke:2px var(--blue)}
.quote cite{display:block;text-align:right;font-style:normal;font-weight:700;margin-top:12px}
.benefits{left:366px;top:372px;width:250px}
.benefits h3{font-size:14px;font-weight:700;color:var(--blue)}
.benefits h3 span{color:var(--ink)}
.benefit{position:relative;padding-left:35px;margin-top:7px;font-size:9px;line-height:1.2;color:#333}
.benefit b{display:block;color:var(--ink);font-size:10px;font-weight:700}
.benefit svg{position:absolute;left:0;top:2px}
.facts{font-size:11px;font-weight:700;line-height:1.8}
.facts em{font-style:normal;color:var(--blue);font-size:12px}
.facts--dates{left:35px;top:648px}
.facts--where{left:350px;top:648px;font-size:9.5px}
.facts--where em{font-size:12px}
.pay-frame{left:33px;top:715px;width:588px;height:37px;border:1px solid #999;border-radius:3px}
.pills{left:93px;top:697px;display:flex;gap:5px}
.pill{height:34px;padding:0 24px;border-radius:8px;background:var(--grey);font-size:11.5px;font-weight:600;display:flex;align-items:center}
.pill--on{background:var(--navy);color:#fff}
.pay-label{left:190px;top:740px;padding:0 6px;background:var(--paper);font-size:15px;font-weight:700;letter-spacing:.3px}
.foot{left:0;top:775px;width:653px;height:68px}
.foot-call{left:30px;top:786px;color:var(--sky);font-size:15px;font-weight:600;line-height:1.1}
.foot-call span{display:block;color:#fff;font-weight:400;font-size:16px}
.foot-links{left:178px;top:790px;color:#fff;font-size:13px;line-height:1.2}
.foot-links div{display:flex;align-items:center;gap:4px}
.foot-tag{left:422px;top:791px;width:215px;font-size:10.5px;line-height:1.25}

/* back */
.back-top{left:0;top:0;width:653px;height:480px;background:var(--navy)}
.back-title{left:40px;top:38px;width:573px;text-align:center;color:#fff;font-size:16.5px;font-weight:700;line-height:1.3}
.photo{background:linear-gradient(160deg,#8aa66b,#5b7a4a 55%,#c9b9a6);border:3px solid #fff}
.photo--one{left:46px;top:103px;width:184px;height:148px}
.photo--two{left:428px;top:268px;width:184px;height:158px;background:linear-gradient(160deg,#3a2c2c,#8a5a4a 55%,#c69a86)}
.bio{color:#fff;font-size:8.6px;line-height:1.32;text-align:justify}
.bio h4{font-size:18px;font-weight:700;color:var(--sky);line-height:1.1}
.bio h5{font-size:15px;font-weight:400;margin-bottom:4px;line-height:1.2}
.bio--one{left:248px;top:101px;width:363px}
.bio--two{left:46px;top:285px;width:365px;text-align-last:right}
.bio--two h4,.bio--two h5{text-align:right}
.tab{left:53px;top:447px;width:547px;height:45px;background:var(--blue);border-radius:6px;color:#fff;font-size:10.5px;font-weight:700;text-align:center;line-height:1.3;padding-top:9px}
.questions{left:48px;top:523px;display:flex;gap:14px}
.qcard{position:relative;width:178px;height:61px;background:var(--card);border-radius:6px;font-size:8.8px;font-weight:500;text-align:center;line-height:1.2;padding:20px 12px 0}
.qcard::after{content:"?";position:absolute;right:4px;top:-14px;font-size:28px;font-weight:800;color:var(--blue)}
.testimonial{left:46px;top:607px;width:270px;height:98px;border:1px solid #555;border-radius:8px;padding:18px 10px 0;font-size:9px;line-height:1.2;color:#333}
.testimonial .mark{position:absolute;left:2px;top:-12px;padding:0 3px;background:var(--paper);font-size:30px;font-weight:700;color:var(--paper);-webkit-text-stroke:1.5px var(--blue);line-height:.8;height:22px;overflow:hidden}
.testimonial cite{position:absolute;right:-4px;bottom:-8px;background:var(--paper);padding:0 4px;font-style:normal;font-weight:700;color:var(--blue)}
.badges{left:50px;top:722px;display:flex;gap:14px;align-items:center}
.badge{background:#cfd8ec}
.cta{left:352px;top:612px;width:270px}
.cta h3{font-size:18px;font-weight:700;color:var(--blue);line-height:1.2}
.cta p{font-size:11.5px;line-height:1.25;margin-top:2px}
.cta h4{font-size:14px;font-weight:700;margin-top:18px}
.cta h4 span{color:var(--blue)}
.cta ul{list-style:none;margin-top:6px;font-size:11.5px;line-height:1.65}
.cta li{display:flex;align-items:center;gap:8px}
</style>
</head>
<body>

<!-- Front page -->
<div class="sheet sheet--front">
  <div class="page">
    <div class="abs band">
      <p style="top:20px">Transformative conversations for senior healthcare leaders.</p>
      <p style="top:56px">Unlock purpose, engage authentically and amplify your leadership impact.</p>
    </div>
    <div class="abs panel"></div>
    <svg class="abs art" viewBox="0 0 653 360">
      <defs>
        <linearGradient id="team" x1="0" y1="0" x2="1" y2="1">
          <stop offset="0" stop-color="#e6e8ec"/>
          <stop offset=".5" stop-color="#9a8f88"/>
          <stop offset="1" stop-color="#e9ecef"/>
        </linearGradient>
      </defs>
      <polygon points="330,330 400,250 653,185 653,250 540,330" fill="#3c62c4"/>
      <polygon points="486,-10 640,60 640,240 486,330 332,240 332,60" fill="#3c62c4"/>
      <polygon points="486,-28 628,46 628,222 486,306 344,222 344,46" fill="#ffffff"/>
      <polygon role="img" aria-label="Photo of a group of smiling business professionals gathered around a laptop" points="486,-20 620,52 620,218 486,298 352,218 352,52" fill="url(#team)"/>
    </svg>
    <div class="abs brand">Marlow Advisory</div>
    <div class="abs headline">
      <div class="l1">ELEVATE <span>AND</span></div>
      <div class="l2">IGNITE YOUR</div>
      <div class="l3">LEADERSHIP</div>
    </div>

    <div class="abs intro">
      <div class="kicker">ANALYTIC COACHING GROUP<b>FOR SENIOR LEADERS</b></div>
      <p>As a senior leader in healthcare, you’re constantly navigating challenges. <b>But where do you turn for authentic connections, reflection and personal growth?</b></p>
      <p class="just">Rethink your leadership assumptions and approach challenges with fresh creativity. Secure your spot in our exclusive Analytic Coaching Group and ignite your leadership potential.</p>
    </div>
    <div class="abs quote">
      <span class="mark">“</span>
      You bare your heart and share things you wouldn’t under normal circumstances. You get to know each other very quickly. There’s that sort of intense, shared experience that comes from speaking to each other’s lives.
      <cite>-Sarah, Medical Director</cite>
    </div>

    <div class="abs benefits">
      <h3>BENEFITS <span>TO YOU</span></h3>
      <div class="benefit"><svg width="26" height="28" viewBox="0 0 26 28"><polygon points="13,1 25,8 25,20 13,27 1,20 1,8" fill="#3c62c4"/><circle cx="13" cy="14" r="5" fill="none" stroke="#fff" stroke-width="1.5"/></svg><b>Transformative conversations</b>Engage in discussions that spark innovative leadership</div>
      <div class="benefit"><svg width="26" height="28" viewBox="0 0 26 28"><polygon points="13,1 25,8 25,20 13,27 1,20 1,8" fill="#3c62c4"/><path d="M8 18v-5h3v5M12 18v-8h3v8M16 18v-6h3v6" fill="none" stroke="#fff" stroke-width="1.3"/></svg><b>Peer insights</b>Harness fresh insights from peers, enhancing your decision-making and effectiveness</div>
      <div class="benefit"><svg width="26" height="28" viewBox="0 0 26 28"><polygon points="13,1 25,8 25,20 13,27 1,20 1,8" fill="#3c62c4"/><circle cx="13" cy="12" r="4" fill="none" stroke="#fff" stroke-width="1.5"/><path d="M11 17h4v2h-4z" fill="#fff"/></svg><b>Reimagined leadership</b>Channel your creativity and redefine your leadership, personally and professionally</div>
      <div class="benefit"><svg width="26" height="28" viewBox="0 0 26 28"><polygon points="13,1 25,8 25,20 13,27 1,20 1,8" fill="#3c62c4"/><path d="M7 17l4-4 3 3 5-6" fill="none" stroke="#fff" stroke-width="1.5"/></svg><b>Instant 360° insights</b>Gain real-time feedback from trusted peers to enrich your leadership</div>
      <div class="benefit"><svg width="26" height="28" viewBox="0 0 26 28"><polygon points="13,1 25,8 25,20 13,27 1,20 1,8" fill="#3c62c4"/><path d="M8 14l3 3 7-7" fill="none" stroke="#fff" stroke-width="1.8"/></svg><b>Lead authentically</b>Develop effective strategies using the latest insights from group and leadership psychology</div>
    </div>

    <div class="abs facts facts--dates"><em>DATES:</em> 7 FEBRUARY 2024 – 11 DECEMBER 2024<br><em>TIME:</em> 7:30AM - 8:45AM (UK TIME)</div>
    <div class="abs facts facts--where"><em>COMMITMENT:</em> WEDNESDAYS, EVERY 2 WEEKS<br><em>LOCATION:</em> CONNECT FROM ANYWHERE BY MEETLINE</div>

    <div class="abs pay-frame"></div>
    <div class="abs pills">
      <div class="pill">COST: £3350 [UK]</div>
      <div class="pill pill--on">COST: €3900 [EUROPE]</div>
      <div class="pill">A$6530 [AUSTRALIA]</div>
    </div>
    <div class="abs pay-label">PAYMENT OPTIONS AVAILABLE</div>

    <svg class="abs foot" viewBox="0 0 653 68" aria-hidden="true"><rect width="653" height="68" fill="#283a8f"/><polygon points="365,0 653,0 653,58 395,58" fill="#fff"/></svg>
    <div class="abs foot-call">CALL US NOW<span>+61 3 9012 5678</span></div>
    <div class="abs foot-links">
      <div><svg width="10" height="8" viewBox="0 0 10 8"><rect x=".5" y=".5" width="9" height="7" fill="none" stroke="#fff"/><path d="M.5 .5l4.5 4 4.5-4" fill="none" stroke="#fff"/></svg>info@marlowadvisory.com</div>
      <div><svg width="10" height="10" viewBox="0 0 10 10"><circle cx="5" cy="5" r="4.4" fill="none" stroke="#fff"/><path d="M.6 5h8.8M5 .6c-2.5 2.5-2.5 6.3 0 8.8M5 .6c2.5 2.5 2.5 6.3 0 8.8" fill="none" stroke="#fff" stroke-width=".8"/></svg>www.marlowadvisory.com</div>
    </div>
    <div class="abs foot-tag">Secure your spot now and ignite your leadership potential</div>
  </div>
</div>

<!-- Back page -->
<div class="sheet sheet--back">
  <div class="page">
    <div class="abs back-top"></div>
    <div class="abs back-title">EXPERTLY GUIDED BY INSIGHT, ACADEMIC RIGOUR AND<br>PRACTICAL LEADERSHIP STRATEGIES</div>

    <div class="abs photo photo--one" role="img" aria-label="Portrait photo of Professor Edward Lindqvist outdoors"></div>
    <div class="abs bio bio--one">
      <h4>EDWARD LINDQVIST</h4>
      <h5>Professor</h5>
      Professor Edward Lindqvist has 30 years’ experience developing leaders. An award- winning business school professor, group analyst and psychoanalytic psychotherapist, he has taught senior leadership programmes at Northgate University, Kingsbridge College and Southbank University. His extensive leadership experience as a public health service clinical director and consultant psychotherapist inform his work as an IACC accredited executive coach. With a PhD from Crestwood College, he is an expert in melding psychological insights with strategic organisational change
    </div>

    <div class="abs photo photo--two" role="img" aria-label="Portrait photo of Dr Helen Ashworth"></div>
    <div class="abs bio bio--two">
      <h4>DR HELEN ASHWORTH</h4>
      <h5>Psychoanalyst</h5>
      Dr Helen Ashworth is a renowned psychoanalyst, group analyst, consultant psychiatrist and organisational consultant in the health sector. She has 20 years of leadership within the public health service, and she was also the National Director of Therapies for the Meridian Care Group, directing therapy services across 100 UK hospitals. She holds prominent positions as Chair of the Patient Safety Group, Chair of the Working Group on the Effect of Suicide and Homicide on Psychiatrists, and Vice Chair of the Psychotherapy Faculty of the Royal Academy of Psychiatric Medicine.
    </div>

    <div class="abs tab">Engage with global leaders, gain diverse insights and forge lasting bonds.<br>Explore questions such as</div>

    <div class="abs questions">
      <div class="qcard">What kind of leader do I aspire to be in the next chapter of my life and career?</div>
      <div class="qcard">What unique qualities and actions do I offer that no one else can?</div>
      <div class="qcard">How can I galvanise my personal strengths to inspire and motivate others?</div>
    </div>

    <div class="abs testimonial">
      <span class="mark">“</span>
      Through this exceptional coaching, our leadership team elevated its performance to lead the hospital with greater clarity, cohesion and thoughtfulness. Not only do we provide a superior work environment for staff, but better care for our patients.
      <cite>-John, CEO</cite>
    </div>

    <div class="abs badges" aria-label="Accreditation badges">
      <div class="badge" style="width:36px;height:36px;border-radius:50%"></div>
      <div class="badge" style="width:64px;height:28px"></div>
      <div class="badge" style="width:64px;height:28px"></div>
      <div class="badge" style="width:72px;height:24px"></div>
    </div>

    <div class="abs cta">
      <h3>LIMITED SPOTS AVAILABLE</h3>
      <p>Don’t miss this unique opportunity to transform your leadership journey.</p>
      <h4><span>BOOK YOUR FREE</span> DISCOVERY CALL</h4>
      <ul>
        <li><svg width="12" height="9" viewBox="0 0 12 9"><rect width="12" height="9" fill="#3c62c4"/><path d="M0 0l6 5 6-5" fill="none" stroke="#fff"/></svg>edward@marlowadvisory.com</li>
        <li><svg width="12" height="9" viewBox="0 0 12 9"><rect width="12" height="9" fill="#3c62c4"/><path d="M0 0l6 5 6-5" fill="none" stroke="#fff"/></svg>h.ashworth@mailpost.net</li>
        <li><svg width="12" height="12" viewBox="0 0 12 12"><circle cx="6" cy="6" r="5.3" fill="none" stroke="#3c62c4"/><path d=".7 6h10.6M6 .7c-3 3-3 7.6 0 10.6M6 .7c3 3 3 7.6 0 10.6" fill="none" stroke="#3c62c4" stroke-width=".9"/></svg>www.marlowadvisory.com</li>
      </ul>
    </div>

    <svg class="abs foot" viewBox="0 0 653 68" aria-hidden="true"><rect width="653" height="68" fill="#283a8f"/><polygon points="375,0 653,0 653,58 405,58" fill="#fff"/></svg>
    <div class="abs foot-call">CALL US NOW<span>+61 3 9012 5678</span></div>
    <div class="abs foot-links">
      <div><svg width="10" height="8" viewBox="0 0 10 8"><rect x=".5" y=".5" width="9" height="7" fill="none" stroke="#fff"/><path d="M.5 .5l4.5 4 4.5-4" fill="none" stroke="#fff"/></svg>info@marlowadvisory.com</div>
      <div><svg width="10" height="10" viewBox="0 0 10 10"><circle cx="5" cy="5" r="4.4" fill="none" stroke="#fff"/><path d="M.6 5h8.8M5 .6c-2.5 2.5-2.5 6.3 0 8.8M5 .6c2.5 2.5 2.5 6.3 0 8.8" fill="none" stroke="#fff" stroke-width=".8"/></svg>www.marlowadvisory.com</div>
    </div>
    <div class="abs foot-tag" style="left:432px">Secure your spot now and ignite your leadership potential</div>
  </div>
</div>

</body>
</html>
```